Bench Advertisement - We Buy Houses Design Needed

Need a catchy, simple but elegant design for bus benches to advertise our company.

We need our website, or phone number, and a smal description (1-2 bulletpoints of what we do and what we offer)

The tricky part is for the designer to fit everything and make the website name as part of the title and fitting everything so that people passing by on the street can see what we offer.

Our website is quickdealhomebuyer.com - (916) 555-0143

Something simple but something that catches the eye of walking pedestrians, and drivers driving by the bench.

Our company buys houses, any condition, any situation, we buy houses for cash and close quickly. You can use this description to create a few bulletpoints however you like. Must follow dimensions in attachment.

Target Market(s)

People in foreclosure, about to lose their homes, people that need a quick cash sale of their property

Industry/Entity Type

Real Estate

Requirements
Must have
• catchy, website name, phone number, few brief bulletpoints about what we offer, colors that will catch peoples eye while walking or driving - advertisement will be placed on bus benches - visit our website to see the type of houses we buy - Also have more work for winner of design with possible bonuses
Nice to have
• Feel free to use description or images on our website - make sure the description is just bullet points and it fits with the overall theme / size of the advertisement - Bold bright colors - put yourself in their shoes (if you were going through financial difficulties and about to lose your house to foreclosure or auction, what would you want to see to pick up the phone and call us for a quick sale of your house?) (or if you have a house that you are having a problem with, problem renters, unkept/beat up house, what would make you want to call us and sell your house to us?)

```html
<!DOCTYPE html>
<html lang="en">
<head>
<meta charset="utf-8">
<title>Quick Deal Home Buyer – Bench Advertisement</title>
<link href="https://fonts.googleapis.com/css2?family=Fjalla+One&family=Open+Sans:wght@400;600;700&display=swap" rel="stylesheet">
<style>
  :root {
    --stage: #2b2b2b;
    --paper: #ffffff;
    --ink-grey: #6d6e70;
    --list-grey: #7a7b7d;
    --accent-orange: #f07f1b;
    --teal-light: #6db6c0;
    --teal-dark: #3d8697;
    --white: #ffffff;
  }
  * { margin: 0; padding: 0; box-sizing: border-box; }
  html, body {
    width: 1200px; height: 768px; overflow: hidden;
    background: var(--stage);
  }
  .bench-ad {
    position: absolute; left: 40px; top: 228px;
    width: 1120px; height: 311px;
    background: var(--paper);
    overflow: hidden;
    font-family: "Open Sans", sans-serif;
  }
  .teal-panel { position: absolute; inset: 0; }
  .offer-list { position: absolute; left: 33px; top: 34px; list-style: none; }
  .offer-list li {
    display: flex; align-items: center; gap: 14px;
    font-family: "Fjalla One", sans-serif;
    font-size: 25px; line-height: 37px;
    color: var(--ink-grey); text-transform: uppercase;
    letter-spacing: 0.2px;
  }
  .offer-list svg { width: 19px; height: 19px; flex: none; }
  .tagline {
    position: absolute; left: 33px; top: 116px;
    font-size: 36px; font-weight: 600; color: var(--accent-orange);
    letter-spacing: 0.3px;
  }
  .steps { position: absolute; left: 33px; top: 168px; list-style: none; }
  .steps li {
    display: flex; align-items: center; gap: 12px;
    font-size: 19px; line-height: 26.5px; color: var(--list-grey);
  }
  .steps svg { width: 23px; height: 23px; flex: none; }
  .brand-name {
    position: absolute; left: 760px; width: 360px; top: 133px;
    text-align: center; color: var(--white);
    font-size: 21px; font-weight: 400; letter-spacing: 0.2px;
    text-transform: uppercase;
  }
  .brand-rule {
    position: absolute; left: 815px; top: 166px;
    width: 195px; height: 2px; background: var(--white);
  }
  .phone {
    position: absolute; right: 30px; top: 198px;
    color: var(--white); font-size: 45px; font-weight: 700;
    line-height: 50px; letter-spacing: 0.3px;
  }
  .website {
    position: absolute; right: 32px; top: 249px;
    color: var(--white); font-size: 23px; font-weight: 600;
    line-height: 28px; letter-spacing: 0.2px;
  }
</style>
</head>
<body>
<main class="bench-ad">
  <svg class="teal-panel" viewBox="0 0 1120 311" preserveAspectRatio="none" aria-hidden="true">
    <defs>
      <linearGradient id="tealFade" x1="0" y1="0" x2="0" y2="1">
        <stop offset="0" stop-color="var(--teal-light)"/>
        <stop offset="1" stop-color="var(--teal-dark)"/>
      </linearGradient>
    </defs>
    <polygon points="810,0 1120,0 1120,311 428,311" fill="url(#tealFade)"/>
  </svg>

  <ul class="offer-list">
    <li>
      <svg viewBox="0 0 20 20" aria-hidden="true"><g fill="#3d8697"><rect x="0" y="0" width="8" height="8"/><rect x="11" y="0" width="8" height="8"/><rect x="0" y="11" width="8" height="8"/><rect x="11" y="11" width="8" height="8"/></g></svg>
      Our company buys houses, any condition, any situation
    </li>
    <li>
      <svg viewBox="0 0 20 20" aria-hidden="true"><g fill="#3d8697"><rect x="0" y="0" width="8" height="8"/><rect x="11" y="0" width="8" height="8"/><rect x="0" y="11" width="8" height="8"/><rect x="11" y="11" width="8" height="8"/></g></svg>
      We buy houses for cash &amp; close quickly
    </li>
  </ul>

  <h1 class="tagline">WE MAKE IT SIMPLE</h1>

  <ol class="steps">
    <li>
      <svg viewBox="0 0 24 24" aria-hidden="true"><circle cx="12" cy="12" r="11" fill="#4f9aa8"/><rect x="8" y="7" width="8" height="10" rx="1" fill="none" stroke="#fff" stroke-width="1.4"/><path d="M10 10.5h4M10 13h4" stroke="#fff" stroke-width="1.2"/></svg>
      Fill Out The Form
    </li>
    <li>
      <svg viewBox="0 0 24 24" aria-hidden="true"><circle cx="12" cy="12" r="11" fill="#4f9aa8"/><path d="M8.5 7.5l2 2-1 1.3c.7 1.5 1.9 2.7 3.4 3.4l1.3-1 2 2-1.2 1.3c-3.6-.4-7.3-4.1-7.7-7.7z" fill="#fff"/></svg>
      We’ll Call You Within A Few Hours
    </li>
    <li>
      <svg viewBox="0 0 24 24" aria-hidden="true"><circle cx="12" cy="12" r="11" fill="#4f9aa8"/><path d="M7.5 11h2v6h-2zM10.5 11l2.3-3.8c.8 0 1.3.6 1.1 1.5l-.4 1.6h3c.7 0 1.2.6 1 1.3l-1 4.2c-.2.6-.7 1-1.3 1h-4.7z" fill="#fff"/></svg>
      We Work With You On A Solution
    </li>
    <li>
      <svg viewBox="0 0 24 24" aria-hidden="true"><circle cx="12" cy="12" r="11" fill="#4f9aa8"/><path d="M12 6.5l5.5 5h-1.7V17h-2.6v-3.3h-2.4V17H8.2v-5.5H6.5z" fill="#fff"/></svg>
      Move On With Your Life
    </li>
  </ol>

  <p class="brand-name">Quick Deal Home Buyer</p>
  <div class="brand-rule"></div>

  <p class="phone">Cell (916) 555-0143</p>
  <p class="website">QUICKDEALHOMEBUYER.COM</p>
</main>
</body>
</html>
```